A-Stand Directional Sign Design

Objective:
We need a professional graphic design for an A-Stand sign that will guide customers arriving in our parking lot to our office. The design should be visually clear, welcoming, and aligned with our brand identity.
REQUIREMENTS:
Two versions of the design:
- One with an arrow pointing left
- One with an arrow pointing right
(This allows us to place the A-Stand anywhere and flip the graphic as needed.)
DIMENSIONS:
- Viewable Area: 30" x 40"
BRAND ALIGNMENT:
- Colors, fonts, and overall style should match our website: www.glidemarrow.com
- Clean, modern, and professional look consistent with our aviation/tourism brand
CONTENT:
- Clear directional arrow (left or right depending on version)
- Text: “Office Entrance” or similar concise wording (designers may propose alternatives if they improve clarity)
READABILITY:
- Bold, high-contrast design for visibility from a distance
- Simple layout that avoids clutter
DELIVERABLES:
- Final artwork in print-ready format (PDF preferred)
- Two versions: Arrow Left and Arrow Right
DESIGN GOAL:
Ensure customers can easily find our office upon arrival, while reinforcing glideMARROW’s professional and welcoming brand image.
Target Market(s)
Tourism
Look and feel

```html
<!DOCTYPE html>
<html lang="en">
<head>
<meta charset="utf-8">
<title>glideMARROW A-Stand Directional Signs</title>
<link rel="stylesheet" href="https://fonts.googleapis.com/css2?family=Montserrat:wght@500;800&display=swap">
<style>
  :root {
    --brand-blue: #1d4596;
    --brand-blue-light: #5a7cba;
    --page-bg: #efeff1;
    --sign-white: #ffffff;
    --ghost: #f1f2f4;
  }
  * { box-sizing: border-box; margin: 0; padding: 0; }
  html, body {
    width: 1200px;
    height: 2561px;
    overflow: hidden;
    background: var(--page-bg);
  }
  .canvas {
    width: 1200px;
    height: 2561px;
    display: flex;
    flex-direction: column;
  }
  .version {
    height: 1280.5px;
    display: flex;
    align-items: center;
    justify-content: center;
  }
  .sign {
    position: relative;
    width: 660px;
    height: 880px;
    background: var(--sign-white);
    box-shadow: 0 10px 30px rgba(0,0,0,0.08);
  }
  .sign-border {
    position: absolute;
    inset: 22px;
    border: 2px solid var(--brand-blue);
  }
  .brand-band {
    position: absolute;
    left: 22px;
    right: 22px;
    top: 56px;
    height: 118px;
    background: linear-gradient(90deg, var(--brand-blue) 0%, var(--brand-blue) 60%, var(--brand-blue-light) 100%);
    display: flex;
    align-items: center;
    justify-content: center;
  }
  .brand-name {
    font-family: "Montserrat", sans-serif;
    font-weight: 500;
    font-size: 30px;
    letter-spacing: 1px;
    color: var(--sign-white);
  }
  .ghost-illustration {
    position: absolute;
    left: 40px;
    right: 40px;
    top: 520px;
    height: 300px;
    background: linear-gradient(180deg, rgba(241,242,244,0) 0%, var(--ghost) 50%, rgba(241,242,244,0) 100%);
  }
  .headline {
    position: absolute;
    left: 0;
    right: 0;
    top: 230px;
    text-align: center;
    font-family: "Montserrat", sans-serif;
    font-weight: 800;
    font-size: 98px;
    line-height: 1.12;
    letter-spacing: -4px;
    color: var(--brand-blue);
  }
  .direction-arrow {
    position: absolute;
    left: 125px;
    top: 500px;
    width: 410px;
    height: 350px;
  }
  .direction-arrow path { fill: var(--brand-blue); }
</style>
</head>
<body>
<main class="canvas">
  <section class="version version--right">
    <div class="sign">
      <div class="sign-border"></div>
      <div class="brand-band"><span class="brand-name">glideMARROW</span></div>
      <div class="ghost-illustration" role="img" aria-label="Faint helicopter silhouette in the background"></div>
      <h1 class="headline">OFFICE<br>ENTRANCE</h1>
      <svg class="direction-arrow" viewBox="0 0 410 350" aria-label="Arrow pointing right">
        <path d="M0 125 H260 L170 0 H275 L410 175 L275 350 H170 L260 225 H0 Z"/>
      </svg>
    </div>
  </section>
  <section class="version version--left">
    <div class="sign">
      <div class="sign-border"></div>
      <div class="brand-band"><span class="brand-name">glideMARROW</span></div>
      <div class="ghost-illustration" role="img" aria-label="Faint helicopter silhouette in the background"></div>
      <h1 class="headline">OFFICE<br>ENTRANCE</h1>
      <svg class="direction-arrow" viewBox="0 0 410 350" aria-label="Arrow pointing left">
        <path d="M410 125 H150 L240 0 H135 L0 175 L135 350 H240 L150 225 H410 Z"/>
      </svg>
    </div>
  </section>
</main>
</body>
</html>
```